Modern Social Media Ad for Law Firm

We need a crisp ad for social media for our law firm, The Harlow Group. The ad will adverrtise for car accident and personal injury cases. Our website is rightsideclaims.example. Our phoone number is 555-314-8826. Use a photo of of our building in the background. I want the add to be light and cripsy. Use logo and photo of attorney. Our address is 418 North Birch Avenue at Red Finch Ballpark.

Target Market(s)

We want to car accident cases and injury cases. The ad should say "Car Accident or Injury? Call us." No fee unless we win!

Industry/Entity Type

Legal

Requirements
Must have
• large photo of me. white background. maybe grayed out columns in the background. website at the bottom with phone number. The Harlow Group logo and name at top. Our colors are black and gold with red as an accent color. Should say "Pensacola, FL" at the bottom in small print.
Nice to have
• if you could fade our building into the background that woul dbe nice
Should not have
• no scales of justice -- I want it to be clean, white, crisp, modern

```html
<!DOCTYPE html>
<html lang="en">
<head>
<meta charset="utf-8">
<title>The Harlow Group – Car Accident Ad</title>
<link href="https://fonts.googleapis.com/css2?family=Nunito+Sans:wght@400;600;700;800;900&family=Cinzel:wght@500&display=swap" rel="stylesheet">
<style>
  :root {
    --backdrop: #c8c8c8;
    --paper: #ffffff;
    --ink: #111111;
    --gold: #d69d2f;
    --photo-light: #eceeef;
    --photo-mid: #b9bcc0;
    --photo-dark: #6c7076;
  }
  html, body {
    margin: 0;
    padding: 0;
    width: 873px;
    height: 1200px;
    overflow: hidden;
    background: var(--backdrop);
  }
  .ad {
    position: absolute;
    left: 63px;
    top: 132px;
    width: 748px;
    height: 935px;
    background: var(--paper);
    overflow: hidden;
    font-family: "Nunito Sans", Arial, sans-serif;
    color: var(--ink);
  }
  .brand {
    position: absolute;
    left: 0;
    width: 470px;
    top: 40px;
    text-align: center;
  }
  .brand-mark {
    width: 96px;
    height: 96px;
    margin: 40px auto 62px;
    background: var(--gold);
  }
  .brand-name {
    font-family: "Cinzel", Georgia, serif;
    font-weight: 500;
    font-size: 21px;
    color: var(--ink);
    margin: 0;
    line-height: 1;
  }
  .brand-tagline {
    display: flex;
    align-items: center;
    justify-content: center;
    gap: 8px;
    margin-top: 3px;
    font-size: 13px;
    color: var(--ink);
  }
  .brand-tagline::before,
  .brand-tagline::after {
    content: "";
    width: 60px;
    height: 1px;
    background: #999;
  }
  .attorney-photo {
    position: absolute;
    left: 357px;
    top: 175px;
    width: 391px;
    height: 600px;
    background:
      linear-gradient(to bottom, rgba(255,255,255,0) 70%, var(--paper) 100%),
      linear-gradient(to right, var(--paper) 0%, rgba(255,255,255,0) 30%),
      radial-gradient(ellipse at 65% 55%, var(--photo-dark) 0%, var(--photo-mid) 45%, var(--photo-light) 80%);
  }
  .headline {
    position: absolute;
    left: 0;
    width: 480px;
    text-align: center;
    margin: 0;
    line-height: 1;
  }
  .headline-question {
    top: 330px;
    font-weight: 600;
    font-size: 51px;
    line-height: 62px;
    letter-spacing: -0.5px;
  }
  .headline-call {
    top: 455px;
    font-weight: 900;
    font-size: 63px;
    letter-spacing: -0.5px;
  }
  .phone-pill {
    position: absolute;
    left: 40px;
    top: 535px;
    width: 396px;
    height: 85px;
    border-radius: 30px;
    background: var(--ink);
    color: var(--gold);
    font-weight: 800;
    font-size: 55px;
    line-height: 85px;
    text-align: center;
    letter-spacing: -0.5px;
  }
  .promise-lead {
    top: 640px;
    font-weight: 600;
    font-size: 52px;
    letter-spacing: -0.5px;
  }
  .promise-win {
    top: 700px;
    font-weight: 900;
    font-size: 64px;
    letter-spacing: -0.5px;
  }
  .footer {
    position: absolute;
    left: 0;
    width: 100%;
    top: 818px;
    text-align: center;
  }
  .footer-web {
    font-weight: 600;
    font-size: 30px;
    line-height: 1;
  }
  .footer-address {
    margin-top: 9px;
    font-weight: 400;
    font-size: 21px;
    line-height: 1;
  }
  .footer-city {
    margin-top: 14px;
    font-weight: 600;
    font-size: 14px;
    letter-spacing: 1.2px;
  }
</style>
</head>
<body>
  <main class="ad">
    <div class="attorney-photo" role="img" aria-label="Photo of the attorney in a grey suit and teal tie, arms crossed, with the firm's building fading into the background"></div>

    <header class="brand">
      <div class="brand-mark"></div>
      <p class="brand-name">The Harlow Group, PLLC.</p>
      <div class="brand-tagline">Attorneys At Law</div>
    </header>

    <h1 class="headline headline-question">CAR ACCIDENT<br>OR INJURY?</h1>
    <p class="headline headline-call">CALL US</p>

    <div class="phone-pill">555-314-8826</div>

    <p class="headline promise-lead">NO FEES UNLESS</p>
    <p class="headline promise-win">WE WIN!</p>

    <footer class="footer">
      <div class="footer-web">rightsideclaims.example</div>
      <div class="footer-address">418 North Birch Avenue at Red Finch Ballpark</div>
      <div class="footer-city">PENSACOLA, FL</div>
    </footer>
  </main>
</body>
</html>
```